WE RISE UP - Personal Growth Seminar

The project is collaboration between Desmond Farrow and Marion Pellby. It will combine the skills of both parties to launch an inspirational and motivation Personal Growth Seminar. We are looking for an e-flyer and a general design that we can use in our promotional work

The programme is a one day seminar which will show delegates how to

1) Kick start your life
2) Overcome obstacles and self sabotage
3) Take control of your future
4) Think bigger than you thought possible
5) Increase your confidence and self belief
6) Six steps to WE RISE UP success

Our values for the seminar, that the eflyer should represent are:
Professional
Freedom
Nature (really important theme)
Fun
Honest
Balance
Integrity

We want to GRAB people's attention and then ENGAGE them into booking onto the seminar. We will send over details for the links to the seminar and phone numbers etc later, so they need to be incorporated. The seminar will be held in a hotel called The Harrowmere (nature and growth theme)

The one thing to remember is, to step back from the design and ask yourself would you book the seminar, based on what you see.

Our websites so you can see our current themes are www.marionpellby-example.com and www.desmondfarrow-example.co.uk

Target Market(s)

Adults based in UK, between 25 and 50 years of age.

Industry/Entity Type

Hotel

Requirements
Must have
• Nature theme - growth
Fun but professional

Colours green but more vibrant like grass colour, nothing dull or washed out

Nice to have
• The picture will give you an idea but doesn't need to be used, it is just for guidance.

A Tree theme could be used - perhaps with the WE RISE UP on the branches
Should not have
• Should not include cartoons

Gawdy colours or too much text

```html
<!DOCTYPE html>
<html lang="en">
<head>
<meta charset="utf-8">
<title>WE RISE UP – One Day Seminar</title>
<link href="https://fonts.googleapis.com/css2?family=Nunito:wght@800;900&family=Arimo:wght@400;700&display=swap" rel="stylesheet">
<style>
  :root {
    --grass-light: #b9e27a;
    --grass-mid: #6fbf3a;
    --grass-deep: #2f7d1c;
    --panel-green: #1f7a14;
    --panel-dark: #13560c;
    --title-green: #2e8a1e;
    --ink-dark: #1d4f12;
    --white: #ffffff;
    --paper: #f6f9f2;
    --grey-text: #444c44;
    --title-shadow: #7a8a7a;
  }
  * { margin: 0; padding: 0; box-sizing: border-box; }
  html, body { width: 849px; height: 1200px; overflow: hidden; background: var(--paper); }
  .flyer {
    position: relative; width: 849px; height: 1200px; overflow: hidden;
    font-family: "Arimo", Arial, sans-serif; color: var(--white);
    background: var(--paper);
  }
  .backdrop { position: absolute; inset: 0; }
  .title {
    position: absolute; top: 18px; left: 0; width: 849px; text-align: center;
    font-family: "Nunito", "Arial Rounded MT Bold", sans-serif; font-weight: 900;
    font-size: 104px; line-height: 1; color: var(--white); letter-spacing: 1px;
    text-shadow: 3px 4px 0 var(--title-shadow), 5px 8px 10px rgba(0,0,0,.35);
  }
  .subtitle {
    position: absolute; top: 138px; left: 0; width: 849px; text-align: center;
    font-family: "Nunito", "Arial Rounded MT Bold", sans-serif; font-weight: 800;
    font-size: 74px; line-height: 1; color: var(--title-green);
    text-shadow: 0 2px 6px rgba(255,255,255,.8);
  }
  .intro {
    position: absolute; top: 318px; left: 40px; width: 540px;
    font-size: 35px; line-height: 1.2;
  }
  .benefits {
    position: absolute; top: 478px; left: 40px; width: 540px; list-style: none;
    font-size: 25px; font-weight: 700; line-height: 41px;
  }
  .benefits li::before { content: "•"; margin-right: 16px; }
  .benefits strong { font-family: "Nunito", sans-serif; font-weight: 900; }
  .venue { position: absolute; top: 735px; left: 40px; width: 560px; }
  .venue-lead { font-size: 29px; font-weight: 700; }
  .venue-name { font-size: 50px; font-weight: 700; margin-top: 14px; line-height: 1.05; }
  .venue-address { font-size: 16px; font-weight: 700; margin-top: 14px; }
  .venue-date { font-size: 30px; font-weight: 700; margin-top: 8px; }
  .speaker { position: absolute; left: 618px; width: 220px; color: var(--grey-text); }
  .speaker-photo { display: block; margin: 0 0 16px 56px; }
  .speaker-name { font-size: 24px; font-weight: 700; color: #2b2b2b; margin-bottom: 4px; }
  .speaker-role { font-size: 19px; line-height: 1.25; }
  .speaker--desmond { top: 380px; }
  .speaker--marion { top: 705px; }
  .web-links {
    position: absolute; top: 1098px; left: 0; width: 849px; text-align: center;
    font-size: 27px; font-weight: 700; line-height: 1.3; color: var(--ink-dark);
    text-shadow: 0 1px 3px rgba(255,255,255,.7);
  }
</style>
</head>
<body>
<main class="flyer">
  <svg class="backdrop" width="849" height="1200" viewBox="0 0 849 1200">
    <defs>
      <linearGradient id="grassTop" x1="0" y1="0" x2="0" y2="1">
        <stop offset="0" stop-color="#e4f4c4"/>
        <stop offset=".55" stop-color="#a9d867"/>
        <stop offset="1" stop-color="#4e9e25"/>
      </linearGradient>
      <linearGradient id="panel" x1="0" y1="0" x2="1" y2="1">
        <stop offset="0" stop-color="#2a8a1a"/>
        <stop offset="1" stop-color="#13560c"/>
      </linearGradient>
      <linearGradient id="grassBottom" x1="0" y1="0" x2="0" y2="1">
        <stop offset="0" stop-color="#c9ea8c"/>
        <stop offset="1" stop-color="#7cc443"/>
      </linearGradient>
    </defs>
    <rect class="grass-top" width="849" height="380" fill="url(#grassTop)" role="img" aria-label="Close-up photograph of fresh green grass with dew drops"/>
    <path class="content-panel" d="M0,280 C260,320 540,250 849,270 L849,300 C700,320 620,360 604,440 L600,1090 L0,1090 Z" fill="url(#panel)"/>
    <path class="speaker-panel" d="M849,300 C700,320 620,360 604,440 L600,1090 L849,1090 Z" fill="var(--paper)"/>
    <path class="grass-bottom" d="M0,1080 C250,1060 600,1100 849,1070 L849,1200 L0,1200 Z" fill="url(#grassBottom)" role="img" aria-label="Photograph of sunlit green grass"/>
  </svg>

  <h1 class="title">WE RISE UP</h1>
  <p class="subtitle">one day seminar</p>

  <p class="intro">The programme is a one day seminar which will show delegates how to:-</p>

  <ul class="benefits">
    <li>Kick start your life</li>
    <li>Overcome obstacles and self sabotage</li>
    <li>Take control of your future</li>
    <li>Think bigger than you thought possible</li>
    <li>Increase your confidence and self belief</li>
    <li>Six steps to <strong>WE RISE UP</strong> success</li>
  </ul>

  <section class="venue">
    <p class="venue-lead">The Seminar is to be held at</p>
    <p class="venue-name">The Harrowmere Hotel</p>
    <p class="venue-address">First line of the Address • Street Name • Area • Post code</p>
    <p class="venue-date">On Saturday • 00th • Month • 2011</p>
  </section>

  <section class="speaker speaker--desmond">
    <svg class="speaker-photo" width="130" height="130" viewBox="0 0 130 130" role="img" aria-label="Portrait photograph of Desmond Farrow">
      <circle cx="65" cy="65" r="62" fill="#7d8f9e" stroke="#ffffff" stroke-width="5"/>
    </svg>
    <p class="speaker-name">Desmond Farrow</p>
    <p class="speaker-role">Motivational speaker, professional speaker, inspirational speaker.</p>
  </section>

  <section class="speaker speaker--marion">
    <svg class="speaker-photo" width="130" height="130" viewBox="0 0 130 130" role="img" aria-label="Portrait photograph of Marion Pellby">
      <circle cx="65" cy="65" r="62" fill="#b8b2a8" stroke="#ffffff" stroke-width="5"/>
    </svg>
    <p class="speaker-name">Marion Pellby</p>
    <p class="speaker-role">Change Speaker, Communication Coach and Hypnotherapist.</p>
  </section>

  <p class="web-links">Visit our websites www.marionpellby-example.com<br>and www.desmondfarrow-example.co.uk</p>
</main>
</body>
</html>
```